Business Card Design

Brambleford Hearth is the name of my health coaching business. My tag line is "Where good health meets real life." I will be working with clients one-on-one and in groups. My target clients are women "of a certain age" who want to be more comfortable in their own skin. We will work together in a 6-month program. The coaching sessions will take place in my kitchen. I will also be conducting monthly cooking classes and field trips - to farmer's markets, speciality markets etc.. for my clients.
Updates

the business name is Brambleford Hearth - I'm not sure how the p got in there at the end of the name

Thank you

Please include the website - www.bramblefordhearth-example.com and the tag line:

Where good health meets real life on the business card.

Thank you

Please add the phone number to the business card - sorry, I forgot to state that in the original brief

(555) 217-4860

Target Market(s)

Women "of a certain age" who want to be more comfortable in their own skin

Industry/Entity Type

Cooking

Contact Information for Business Card

Brambleford Hearth
Where good health meets real life

Tessa Marlowe
Health Coach
(555) 217-4860

Font styles to use
Serif
Sans Serif

Requirements
Must have
• front & back design
I typical like soft colors - and have tended toward greens over time - I'm open although I would not like bright reds, yellows etc..

```html
<!DOCTYPE html>
<html lang="en">
<head>
<meta charset="utf-8">
<title>Brambleford Hearth – Business Card Colour Options</title>
<link rel="stylesheet" href="https://fonts.googleapis.com/css2?family=Montserrat:wght@700;800&family=Encode+Sans+Condensed:wght@600&family=PT+Sans:wght@400;700&family=PT+Sans+Narrow&family=Patrick+Hand&display=swap">
<style>
  :root {
    --page-bg: #000000;
    --label: #bfe3b0;
    --card-green: #4f9446;
    --card-sage: #4b8744;
    --pattern-light: rgba(170, 215, 150, 0.22);
    --pattern-dark: rgba(60, 120, 55, 0.25);
    --ink-light: #d2ecc4;
    --name-box: #c9e7bb;
    --name-ink: #3f7a38;
  }
  * { margin: 0; padding: 0; box-sizing: border-box; }
  html, body { width: 1200px; height: 1000px; overflow: hidden; background: var(--page-bg); }
  .canvas { position: relative; width: 1200px; height: 1000px; }

  .option-label {
    position: absolute; left: 0; width: 1200px; text-align: center; color: var(--label);
  }
  .option-label--before { top: 38px; font: 800 40px/1 "Montserrat", sans-serif; letter-spacing: 1px; }
  .option-label--sage { top: 518px; font: 600 52px/1 "Encode Sans Condensed", sans-serif; letter-spacing: -1px; }

  .card {
    position: absolute; width: 503px; height: 278px; overflow: hidden;
    background: var(--card-green); color: var(--ink-light);
  }
  .card--sage { background: var(--card-sage); }
  .card__pattern {
    position: absolute; inset: 0;
    background: linear-gradient(160deg, var(--pattern-light), var(--pattern-dark) 55%, var(--pattern-light));
  }

  .card__name {
    position: absolute; left: 280px; top: 20px; width: 208px; height: 27px;
    background: var(--name-box); color: var(--name-ink);
    font: 700 19px/27px "PT Sans", sans-serif; text-align: right; padding-right: 6px;
  }
  .card__role {
    position: absolute; right: 16px; top: 47px;
    font: 700 19px/24px "PT Sans", sans-serif;
  }
  .card__brand {
    position: absolute; left: 56px; top: 102px; white-space: nowrap;
    font: 400 46px/1 "PT Sans", sans-serif; letter-spacing: -0.5px;
  }
  .card__brand-second { font-size: 31px; letter-spacing: 0.5px; }
  .card__tagline {
    position: absolute; left: 285px; top: 157px;
    font: 400 14px/1 "PT Sans Narrow", sans-serif;
  }

  .contact { position: absolute; top: 214px; text-align: center; }
  .contact__icon { display: block; margin: 0 auto; }
  .contact__rule { height: 2px; background: var(--ink-light); margin-top: 2px; }
  .contact__text {
    display: block; margin-top: 3px; white-space: nowrap;
    font: 400 11px/1 "PT Sans Narrow", sans-serif; letter-spacing: -0.2px;
  }
  .contact--email { left: 14px; width: 150px; }
  .contact--web { left: 172px; width: 156px; }
  .contact--phone { left: 336px; width: 152px; }
  .contact--phone .contact__text { font: 700 14px/1 "PT Sans", sans-serif; letter-spacing: 0.5px; }

  .card__message {
    position: absolute; left: 64px; top: 112px;
    font: 400 19px/25px "Patrick Hand", cursive; letter-spacing: 1px;
  }
  .social { position: absolute; left: 170px; top: 218px; width: 156px; text-align: center; }
  .social__mark { width: 18px; height: 18px; margin: 0 auto; background: var(--ink-light); }
  .social__rule { height: 2px; background: var(--ink-light); margin-top: 5px; }
  .social__handle { display: block; margin-top: 2px; font: 700 14px/1 "Montserrat", sans-serif; letter-spacing: 1.5px; }
</style>
</head>
<body>
<main class="canvas">

  <h2 class="option-label option-label--before">Before</h2>

  <section class="card card--front" style="left:75px; top:115px;">
    <div class="card__pattern" role="img" aria-label="Faint background pattern of kitchenware silhouettes: teapots, cutlery, cups and pans"></div>
    <div class="card__name">Tessa Marlowe</div>
    <div class="card__role">Health Coach</div>
    <div class="card__brand">Brambleford <span class="card__brand-second">Hearth</span></div>
    <div class="card__tagline">where good health meets real life</div>
    <div class="contact contact--email">
      <svg class="contact__icon" width="26" height="22" viewBox="0 0 26 22" fill="none" stroke="currentColor" stroke-width="1.4"><rect x="3" y="6" width="20" height="13"/><path d="M3 6l10 8 10-8"/></svg>
      <div class="contact__rule"></div>
      <span class="contact__text">tessa@bramblefordhearth-example.com</span>
    </div>
    <div class="contact contact--web">
      <svg class="contact__icon" width="26" height="22" viewBox="0 0 26 22" fill="none" stroke="currentColor" stroke-width="1.4"><circle cx="12" cy="11" r="9"/><path d="M3 11h18M12 2v18M12 2c-5 5-5 13 0 18M12 2c5 5 5 13 0 18"/></svg>
      <div class="contact__rule"></div>
      <span class="contact__text">www.bramblefordhearth-example.com</span>
    </div>
    <div class="contact contact--phone">
      <svg class="contact__icon" width="26" height="22" viewBox="0 0 26 22" fill="none" stroke="currentColor" stroke-width="1.4"><rect x="8" y="1" width="10" height="20" rx="2"/><path d="M11 18h4"/></svg>
      <div class="contact__rule"></div>
      <span class="contact__text">(555) 217-4860</span>
    </div>
  </section>

  <section class="card card--back" style="left:648px; top:112px;">
    <div class="card__pattern" role="img" aria-label="Faint background pattern of kitchenware silhouettes: pots, mugs, spoons and knives"></div>
    <p class="card__message">Reach your health and weight loss goals<br>with a plan designed just for you.</p>
    <div class="social">
      <div class="social__mark"></div>
      <div class="social__rule"></div>
      <span class="social__handle">bh_hearth</span>
    </div>
  </section>

  <h2 class="option-label option-label--sage">Sage green</h2>

  <section class="card card--front card--sage" style="left:72px; top:593px;">
    <div class="card__pattern" role="img" aria-label="Faint background pattern of kitchenware silhouettes: teapots, cutlery, cups and pans"></div>
    <div class="card__name">Tessa Marlowe</div>
    <div class="card__role">Health Coach</div>
    <div class="card__brand">Brambleford <span class="card__brand-second">Hearth</span></div>
    <div class="card__tagline">where good health meets real life</div>
    <div class="contact contact--email">
      <svg class="contact__icon" width="26" height="22" viewBox="0 0 26 22" fill="none" stroke="currentColor" stroke-width="1.4"><rect x="3" y="6" width="20" height="13"/><path d="M3 6l10 8 10-8"/></svg>
      <div class="contact__rule"></div>
      <span class="contact__text">tessa@bramblefordhearth-example.com</span>
    </div>
    <div class="contact contact--web">
      <svg class="contact__icon" width="26" height="22" viewBox="0 0 26 22" fill="none" stroke="currentColor" stroke-width="1.4"><circle cx="12" cy="11" r="9"/><path d="M3 11h18M12 2v18M12 2c-5 5-5 13 0 18M12 2c5 5 5 13 0 18"/></svg>
      <div class="contact__rule"></div>
      <span class="contact__text">www.bramblefordhearth-example.com</span>
    </div>
    <div class="contact contact--phone">
      <svg class="contact__icon" width="26" height="22" viewBox="0 0 26 22" fill="none" stroke="currentColor" stroke-width="1.4"><rect x="8" y="1" width="10" height="20" rx="2"/><path d="M11 18h4"/></svg>
      <div class="contact__rule"></div>
      <span class="contact__text">(555) 217-4860</span>
    </div>
  </section>

  <section class="card card--back card--sage" style="left:649px; top:596px;">
    <div class="card__pattern" role="img" aria-label="Faint background pattern of kitchenware silhouettes: pots, mugs, spoons and knives"></div>
    <p class="card__message">Reach your health and weight loss goals<br>with a plan designed just for you.</p>
    <div class="social">
      <div class="social__mark"></div>
      <div class="social__rule"></div>
      <span class="social__handle">bh_hearth</span>
    </div>
  </section>

</main>
</body>
</html>
```